Open sky harmony Business cards - yoga studio

We need business cards for our yoga studio Opensky Harmony.
We would like to see designs that include the colour blue and our logo.
The business card should communicate a feeling of strength and calm

Requirements
Must have
• The business card must include
"Mirela Thornquist - Director"
and
"42 Wattlecrest Avenue
Dunmoreton
VIC 3917
Ph - 0471 586 204"

```html
<!DOCTYPE html>
<html lang="en">
<head>
<meta charset="utf-8">
<title>Opensky Harmony – Business Cards</title>
<link rel="stylesheet" href="https://fonts.googleapis.com/css2?family=Open+Sans:wght@300;400;600&display=swap">
<style>
  :root {
    --backdrop: #ebe8e5;
    --card-white: #fbfbfb;
    --teal: #5aa9b9;
    --teal-ink: #4d9fb0;
    --ink: #1f2a2d;
    --white: #ffffff;
    --shadow: rgba(60, 50, 40, 0.16);
  }
  * { margin: 0; padding: 0; box-sizing: border-box; }
  html, body {
    width: 1200px; height: 997px; overflow: hidden;
    background: var(--backdrop);
    font-family: "Open Sans", Arial, sans-serif;
  }
  .card-set {
    position: relative; width: 1200px; height: 997px;
    display: flex; align-items: center; justify-content: center; gap: 70px;
  }
  .card {
    position: relative; width: 500px; height: 286px;
    border-radius: 3px;
    box-shadow: 0 10px 26px var(--shadow);
    overflow: hidden;
  }
  /* Front */
  .card-front {
    background: var(--card-white);
    display: flex; flex-direction: column; align-items: center; justify-content: center;
  }
  .brand-lockup { display: flex; align-items: center; gap: 14px; }
  .brand-dot {
    width: 22px; height: 22px; border-radius: 50%; background: var(--teal-ink);
  }
  .brand-name {
    color: var(--teal-ink); font-weight: 300; font-size: 38px; letter-spacing: 0.5px;
  }
  .brand-tagline {
    margin-top: 8px; color: var(--teal-ink); font-weight: 300;
    font-size: 11px; letter-spacing: 3px; text-transform: uppercase;
  }
  /* Back */
  .card-back { background: var(--teal); }
  .person {
    position: absolute; top: 24px; right: 26px; text-align: right;
  }
  .person-name { color: var(--white); font-size: 17px; font-weight: 400; }
  .person-role { color: var(--ink); font-size: 14px; margin-top: 4px; }
  .brand-feature {
    position: absolute; left: 190px; top: 112px;
    color: var(--white); font-weight: 300; font-size: 30px; line-height: 1.1;
  }
  .contact {
    position: absolute; left: 26px; bottom: 22px;
    color: var(--ink); font-size: 13.5px; line-height: 1.35;
    font-style: normal;
  }
</style>
</head>
<body>
  <main class="card-set">
    <section class="card card-front" aria-label="Card front">
      <div class="brand-lockup">
        <span class="brand-dot"></span>
        <span class="brand-name">Opensky Harmony</span>
      </div>
      <p class="brand-tagline">Yoga • Fitness • Aqua</p>
    </section>

    <section class="card card-back" aria-label="Card back">
      <div class="person">
        <p class="person-name">Mirela Thornquist</p>
        <p class="person-role">Director</p>
      </div>
      <p class="brand-feature">Opensky<br>Harmony</p>
      <address class="contact">
        42 Wattlecrest Avenue<br>
        Dunmoreton, VIC 3917<br>
        ph 0471 586 204
      </address>
    </section>
  </main>
</body>
</html>
```